Shopify Web-Page "Tiny-ThreadDays

We are building a new business in Switzerland offering premium sewing holiday camps for kids aged 9–14. In enclosed brief outlines our requirements for a complete Shopify homepage design and a multilingual logo creation.
Domains: tiny-threaddays.ch ; tiny-giornifilo.ch ; tiny-fadentage.ch

Project Overview
We are looking for:
1. A modern, fully designed Shopify homepage in English using standard Shopify content blocks (no custom coding), which we can later update ourselves. Supporting Multilanguage (EN, German, Italian).

2. A logo design that includes the brand identity and communicates our multilingual, creative, and child-focused positioning.

All details in enclosed

```html
<!DOCTYPE html>
<html lang="en">
<head>
<meta charset="utf-8">
<title>Tiny-ThreadDays – Sewing Holiday Camps for Kids</title>
<link href="https://fonts.googleapis.com/css2?family=Roboto:wght@400;500;700&display=swap" rel="stylesheet">
<style>
:root{
  --orange:#f4471e;
  --black:#000;
  --ink:#111;
  --muted:#8a8a8a;
  --page:#f0f0f0;
  --card:#f6f6f6;
  --white:#fff;
  --rule:#d6d6d6;
}
*{margin:0;padding:0;box-sizing:border-box}
html,body{width:1200px;height:4971px;overflow:hidden}
body{position:relative;background:var(--page);font-family:'Roboto',sans-serif;color:var(--ink)}
.abs{position:absolute}
.btn{position:absolute;display:flex;align-items:center;justify-content:space-between;padding:0 22px;border-radius:30px;font-size:16px;font-weight:500}
.btn svg{width:20px;height:12px}
.btn-orange{background:var(--orange);color:var(--white)}
.btn-white{background:var(--white);color:var(--ink)}
.eyebrow{position:absolute;color:var(--orange);font-size:20px;font-weight:500;text-transform:uppercase}
.heading{position:absolute;font-size:42px;font-weight:500;line-height:60px}

/* top bar */
.announce{top:0;left:0;width:1200px;height:42px;background:var(--orange);color:var(--white);font-size:17px;display:flex;align-items:center;justify-content:center}

/* hero */
.hero{top:42px;left:0;width:1200px;height:600px;background:linear-gradient(180deg,#2a2620 0%,#4a3c2e 45%,#3a3128 100%)}
.util{top:75px;font-size:14px;color:var(--white)}
.util-line{top:102px;left:0;width:1200px;height:1px;background:rgba(255,255,255,.15)}
.brand{top:118px;left:112px;font-size:24px;font-weight:500;color:var(--white)}
.nav{top:126px;left:413px;display:flex;gap:20px;font-size:14px;color:var(--white)}
.nav .active{color:var(--orange)}
.hero-title{top:248px;left:112px;font-size:46px;font-weight:700;line-height:66px;color:var(--white)}

/* steps */
.step-icon{position:absolute;width:78px;height:78px;border-radius:50%;background:var(--black);display:flex;align-items:center;justify-content:center}
.step-icon svg{width:40px;height:40px}
.step-title{position:absolute;font-size:18px;font-weight:500;line-height:26px;width:170px}
.step-rule{position:absolute;width:154px;height:1px;background:var(--rule)}
.step-text{position:absolute;font-size:14px;line-height:26px;color:var(--muted);width:200px}

/* dark bands */
.band{position:absolute;left:0;width:700px;background:var(--black);border-bottom-right-radius:100px}
.photo{position:absolute;left:613px;width:587px;height:584px;border-radius:110px 0 0 110px}
.band-text{position:absolute;color:var(--white)}
.about-copy{top:1695px;left:112px;width:420px;font-size:14px;line-height:28px;text-align:justify}
.faq-list{top:3016px;left:112px;list-style:none;font-size:16px;line-height:43px}
.faq-list li::before{content:"+";margin-right:10px;font-weight:700}

/* why cards */
.why-card{position:absolute;top:2320px;width:150px;height:284px;border-radius:18px;background:var(--card);text-align:center}
.why-card.raised{background:#f8f8f8;box-shadow:0 4px 14px rgba(0,0,0,.12)}
.why-icon{width:86px;height:86px;border-radius:50%;background:var(--orange);margin:32px auto 0;display:flex;align-items:center;justify-content:center}
.why-icon svg{width:44px;height:44px}
.why-label{margin:22px 14px 0;font-size:14px;font-weight:500;line-height:21px}

/* camps */
.camp{position:absolute;top:3623px;width:239px;height:351px;background:var(--white);border-radius:12px}
.camp-photo{width:239px;height:240px;border-radius:12px 12px 0 0}
.camp-avatar{position:absolute;top:214px;right:22px;width:52px;height:52px;border-radius:50%;background:#9a8c80;border:3px solid var(--white)}
.camp-name{position:absolute;top:262px;left:17px;font-size:18px;font-weight:500}
.camp-date{position:absolute;top:292px;left:17px;font-size:12px;color:#555}

/* newsletter */
.newsletter{top:4051px;left:0;width:1200px;height:511px;background:linear-gradient(135deg,#1d2333 0%,#2e2a30 50%,#1a1c26 100%)}
.field{position:absolute;height:58px;border-radius:29px;background:var(--white);font-size:12px;color:#444;display:flex;align-items:center;padding-left:20px}

/* footer */
.footer{top:4562px;left:0;width:1200px;height:409px;background:var(--black)}
.foot-head{position:absolute;top:4636px;font-size:24px;font-weight:500;color:var(--white)}
.foot-links{position:absolute;top:4688px;left:438px;list-style:none;font-size:14px;line-height:34px;color:var(--white)}
.contact{position:absolute;left:714px;font-size:14px;line-height:22px;color:var(--white);display:flex;gap:16px}
.contact svg{width:14px;height:14px;flex:none;margin-top:4px}
.social{position:absolute;top:4764px;width:36px;height:36px;border-radius:50%;background:var(--white)}
</style>
</head>
<body>

<div class="abs announce">Nemo enim ipsam voluptatem</div>

<header class="abs hero" role="img" aria-label="Photo of children at a camp workshop tying cords, with a dark overlay"></header>
<div class="abs util" style="left:112px">info@tiny-threaddays.ch</div>
<div class="abs util" style="left:316px">+41 44 555 12 34</div>
<div class="abs util" style="left:900px;display:flex;align-items:center;gap:6px">
  <svg width="11" height="12" viewBox="0 0 11 12"><circle cx="5.5" cy="3.2" r="3" fill="#fff"/><path d="M0 12c0-3.5 2.5-5 5.5-5s5.5 1.5 5.5 5z" fill="#fff"/></svg>My Account</div>
<div class="abs util" style="left:1032px;display:flex;align-items:center;gap:6px">
  <svg width="13" height="13" viewBox="0 0 13 13"><circle cx="6.5" cy="6.5" r="6" fill="#fff"/><path d="M6.5 .5v12M.5 6.5h12" stroke="#333" stroke-width="1"/></svg>EN
  <svg width="9" height="6" viewBox="0 0 9 6"><path d="M1 1l3.5 3.5L8 1" fill="none" stroke="#fff" stroke-width="1.4"/></svg></div>
<div class="abs util-line"></div>
<div class="abs brand">Tiny-ThreadDays</div>
<nav class="abs nav"><span class="active">Home</span><span>About Us</span><span>How its Work</span><span>Trust-building</span><span>Upcoming Camp</span></nav>
<h1 class="abs hero-title">Where Creativity Meets<br>Adventure!</h1>
<div class="btn btn-orange" style="top:413px;left:112px;width:244px;height:52px">Get Started<svg viewBox="0 0 20 12"><path d="M0 6h17M12 1l6 5-6 5" fill="none" stroke="#fff" stroke-width="2"/></svg></div>

<!-- steps -->
<div class="eyebrow" style="top:732px;left:0;width:1200px;text-align:center">Step by step</div>
<h2 class="heading" style="top:760px;left:0;width:1200px;text-align:center">What kids do During The Camp</h2>

<div class="step-icon" style="top:916px;left:112px"><svg viewBox="0 0 40 40" fill="none" stroke="#fff" stroke-width="2"><circle cx="20" cy="17" r="9"/><path d="M16 28h8M17 32h6M20 4v3M8 8l2 2M32 8l-2 2"/></svg></div>
<div class="step-title" style="top:910px;left:203px">Project selection</div>
<div class="step-rule" style="top:978px;left:203px"></div>
<div class="step-text" style="top:994px;left:203px">Your child chooses their own model based on previously produced clothing items and sewing patterns.</div>

<div class="step-icon" style="top:916px;left:470px"><svg viewBox="0 0 40 40" fill="none" stroke="#fff" stroke-width="2"><path d="M6 14h28v6H6zM6 20l4 8h20l4-8M10 14v6M16 14v6M22 14v6M28 14v6"/></svg></div>
<div class="step-title" style="top:910px;left:561px">Fabric Selection</div>
<div class="step-rule" style="top:978px;left:561px"></div>
<div class="step-text" style="top:994px;left:561px;width:170px">High-quality fabrics are available.</div>

<div class="step-icon" style="top:916px;left:828px"><svg viewBox="0 0 40 40" fill="none" stroke="#fff" stroke-width="2"><path d="M10 6v28M18 6v28M26 6v28M32 6v20"/><circle cx="10" cy="20" r="3"/><circle cx="26" cy="16" r="3"/></svg></div>
<div class="step-title" style="top:910px;left:919px">Sewing Machine operation</div>
<div class="step-rule" style="top:978px;left:919px"></div>
<div class="step-text" style="top:994px;left:919px;width:150px">Learn how to use a sewing machine</div>

<div class="step-icon" style="top:1158px;left:112px"><svg viewBox="0 0 40 40" fill="none" stroke="#fff" stroke-width="2"><path d="M8 32L30 10M12 34L34 12M10 20c4-6 10-8 14-4"/><circle cx="30" cy="10" r="2"/></svg></div>
<div class="step-title" style="top:1153px;left:203px">Sewing &amp; Refining</div>
<div class="step-rule" style="top:1222px;left:203px"></div>
<div class="step-text" style="top:1238px;left:203px;width:170px">Step by step to the goal with professional guidance</div>

<div class="step-icon" style="top:1158px;left:470px"><svg viewBox="0 0 40 40" fill="none" stroke="#fff" stroke-width="2"><rect x="6" y="8" width="28" height="24" rx="2"/><path d="M6 15h28M12 5v6M28 5v6M11 21h4M18 21h4M25 21h4M11 27h4M18 27h4"/></svg></div>
<div class="step-title" style="top:1153px;left:561px">Showtime!</div>
<div class="step-rule" style="top:1222px;left:561px"></div>
<div class="step-text" style="top:1238px;left:561px;width:170px">Fashion show or photo shoot at the end of the week</div>

<!-- about -->
<div class="band" style="top:1456px;height:604px"></div>
<div class="photo" style="top:1380px;background:linear-gradient(160deg,#6f8a4a 0%,#b9c3cc 40%,#c7412e 70%,#6b4a36 100%)" role="img" aria-label="Photo of a child holding red yarn beside balls of wool"></div>
<div class="eyebrow" style="top:1515px;left:112px">About us</div>
<h2 class="heading band-text" style="top:1552px;left:112px">Instructors and The<br>Camp Philosophy</h2>
<p class="band-text about-copy">Lena and Mara have over 10 years of experience in teaching children sewing, tailoring, and design with fun, style, and structure. In small groups (max. 8 children), we guide young talents through a creative week of vacation – with real results: self-sewn pieces, new friends, and lots of pride.<br>At the last day, the children show off their success, their own sewn unique pieces, in a symapatic fashion show.</p>
<div class="btn btn-white" style="top:1928px;left:112px;width:222px;height:50px">Read More<svg viewBox="0 0 20 12"><path d="M0 6h17M12 1l6 5-6 5" fill="none" stroke="#111" stroke-width="2"/></svg></div>

<!-- why -->
<div class="eyebrow" style="top:2182px;left:112px">Trust-building</div>
<h2 class="heading" style="top:2218px;left:115px">Why Parents Choose Us</h2>

<div class="why-card raised" style="left:112px"><div class="why-icon"><svg viewBox="0 0 44 44" fill="none" stroke="#fff" stroke-width="2"><rect x="8" y="10" width="28" height="26" rx="2"/><path d="M8 18h28M14 24h4M20 24h4M26 24h4M14 30h4M20 30h4"/></svg></div><div class="why-label">Small groups &amp; personalized attention</div></div>
<div class="why-card" style="left:277px"><div class="why-icon"><svg viewBox="0 0 44 44" fill="none" stroke="#fff" stroke-width="2"><rect x="8" y="8" width="18" height="24" rx="2"/><rect x="18" y="14" width="18" height="24" rx="2"/><path d="M22 22h10M22 28h10"/></svg></div><div class="why-label">Multilingual supervision (DE / EN / IT)</div></div>
<div class="why-card" style="left:442px"><div class="why-icon"><svg viewBox="0 0 44 44" fill="none" stroke="#fff" stroke-width="2"><path d="M8 16h28v8H8zM10 24l4 10h16l4-10M14 16V8M22 16V8M30 16V8"/></svg></div><div class="why-label">High-quality fabrics &amp; top-quality sewing machines (Swiss-made)</div></div>
<div class="why-card" style="left:607px"><div class="why-icon"><svg viewBox="0 0 44 44" fill="none" stroke="#fff" stroke-width="2"><path d="M10 30l8-14 4 6 4-6 8 14zM22 8v6M14 10l2 4M30 10l-2 4"/></svg></div><div class="why-label">Encouragement of creativity, self-confidence, and fine motor skills</div></div>
<div class="why-card" style="left:772px"><div class="why-icon"><svg viewBox="0 0 44 44" fill="none" stroke="#fff" stroke-width="2"><path d="M22 32s-10-6-10-13a5 5 0 0 1 10-2 5 5 0 0 1 10 2c0 7-10 13-10 13zM6 30c6 0 8 6 16 6s10-6 16-6"/></svg></div><div class="why-label">Safe, loving environment in Zurich, various places easy to reach</div></div>
<div class="why-card" style="left:937px"><div class="why-icon"><svg viewBox="0 0 44 44" fill="none" stroke="#fff" stroke-width="2"><rect x="8" y="18" width="22" height="12" rx="2"/><path d="M30 22h6v8h-6M6 34h32"/><circle cx="30" cy="10" r="3"/></svg></div><div class="why-label">Pick-up Service from the Main-Station</div></div>

<!-- faq -->
<div class="band" style="top:2780px;height:602px"></div>
<div class="photo" style="top:2701px;background:linear-gradient(150deg,#d9d1c6 0%,#a8876a 45%,#5b4a5e 75%,#2e2c3a 100%)" role="img" aria-label="Photo of two children crafting together at a table"></div>
<div class="eyebrow" style="top:2838px;left:112px">We're here to help</div>
<h2 class="heading band-text" style="top:2875px;left:112px">Frequently Asked<br>Questions</h2>
<ul class="band-text faq-list">
  <li>Does my child need any prior knowledge?</li>
  <li>How many items of clothing are produced?</li>
  <li>How does the pick-up service work?</li>
  <li>How does the pick-up service work?</li>
  <li>How does the pick-up service work?</li>
</ul>
<div class="btn btn-orange" style="top:3250px;left:112px;width:222px;height:50px">View More<svg viewBox="0 0 20 12"><path d="M0 6h17M12 1l6 5-6 5" fill="none" stroke="#fff" stroke-width="2"/></svg></div>

<!-- camps -->
<div class="eyebrow" style="top:3482px;left:0;width:1200px;text-align:center">Upcoming</div>
<h2 class="heading" style="top:3520px;left:0;width:1200px;text-align:center">Upcoming Camp Offerings</h2>

<div class="camp" style="left:112px"><div class="camp-photo" style="background:linear-gradient(160deg,#5e7a86,#8d6b4f 60%,#3c5a63)" role="img" aria-label="Photo of a boy at a campsite"></div><div class="camp-avatar" role="img" aria-label="Instructor portrait"></div><div class="camp-name">Spring Camps</div><div class="camp-date">Sep 13,2025</div></div>
<div class="camp" style="left:358px"><div class="camp-photo" style="background:linear-gradient(160deg,#4f6a4a,#6e6a5c 55%,#3a4034)" role="img" aria-label="Photo of scouts tying ropes"></div><div class="camp-avatar" role="img" aria-label="Instructor portrait"></div><div class="camp-name">Summer Camps</div><div class="camp-date">Sep 13,2025</div></div>
<div class="camp" style="left:604px"><div class="camp-photo" style="background:linear-gradient(160deg,#e0622e,#d99a6e 55%,#6c5540)" role="img" aria-label="Photo of children in a tent"></div><div class="camp-avatar" role="img" aria-label="Instructor portrait"></div><div class="camp-name">Nemo Enim</div><div class="camp-date">Sep 13,2025</div></div>
<div class="camp" style="left:850px"><div class="camp-photo" style="background:linear-gradient(160deg,#2d5a2b,#c2283a 50%,#e7d9c8)" role="img" aria-label="Photo of children playing on a blanket"></div><div class="camp-avatar" role="img" aria-label="Instructor portrait"></div><div class="camp-name">Nemo Enim</div><div class="camp-date">Sep 13,2025</div></div>

<!-- newsletter -->
<section class="abs newsletter" role="img" aria-label="Dark photo background of children crafting"></section>
<h2 class="heading" style="top:4116px;left:0;width:1200px;text-align:center;color:#fff">Register for Newsletter</h2>
<p class="abs" style="top:4190px;left:0;width:1200px;text-align:center;font-size:16px;color:#fff">Promotions, new products and sales. Directly to your inbox.</p>
<div class="field" style="top:4252px;left:258px;width:324px">First Name</div>
<div class="field" style="top:4252px;left:618px;width:324px">Last Name</div>
<div class="field" style="top:4330px;left:258px;width:684px">Email Address</div>
<div class="btn btn-orange" style="top:4416px;left:477px;width:246px;height:50px">Submit Now<svg viewBox="0 0 20 12"><path d="M0 6h17M12 1l6 5-6 5" fill="none" stroke="#fff" stroke-width="2"/></svg></div>

<!-- footer -->
<footer class="abs footer"></footer>
<div class="abs" style="top:4668px;left:148px;font-size:24px;font-weight:500;line-height:34px;color:#fff">Tiny-<br>ThreadDays</div>
<div class="social" style="left:134px;background:var(--orange)" aria-label="Social profile"></div>
<div class="social" style="left:181px" aria-label="Social profile"></div>
<div class="social" style="left:228px" aria-label="Social profile"></div>
<div class="social" style="left:275px" aria-label="Social profile"></div>
<div class="social" style="left:322px" aria-label="Social profile"></div>

<div class="foot-head" style="left:433px">Quick Links</div>
<ul class="foot-links"><li>Home</li><li>About Us</li><li>How its Work</li><li>Trust-building</li><li>Upcoming Camp</li></ul>

<div class="foot-head" style="left:714px">Contact Us</div>
<div class="contact" style="top:4690px"><svg viewBox="0 0 14 14"><path d="M7 13s-5-5-5-8a5 5 0 0 1 10 0c0 3-5 8-5 8z" fill="#f4471e"/><circle cx="7" cy="5" r="1.8" fill="#000"/></svg><span style="width:320px">125455 ipsam voluptatem quia voluptas sit aspernatur aut 255</span></div>
<div class="contact" style="top:4751px"><svg viewBox="0 0 14 14"><rect x="1" y="3" width="12" height="8" fill="#f4471e"/><path d="M1 3l6 5 6-5" fill="none" stroke="#000" stroke-width="1"/></svg><span>info@tiny-threaddays.ch</span></div>
<div class="contact" style="top:4798px"><svg viewBox="0 0 14 14"><path d="M3 1l3 3-1.5 2a8 8 0 0 0 3.5 3.5L10 8l3 3-2 2C6 13 1 8 1 3z" fill="#f4471e"/></svg><span>+41 44 555 12 34</span></div>

<div class="btn btn-orange" style="top:4860px;left:875px;width:210px;height:48px">Book Now<svg viewBox="0 0 20 12"><path d="M0 6h17M12 1l6 5-6 5" fill="none" stroke="#fff" stroke-width="2"/></svg></div>
<p class="abs" style="top:4926px;left:0;width:1200px;text-align:center;font-size:14px;color:#fff">© 2025 Company Name. All Rights Reserved.</p>

</body>
</html>
```